Before the kettle boils, pocast with content in its majority of technology

Page dedicated to a pocast with content in its majority of technology. The page also contains the chapters of the podcast (pluggin vocalink) will also contain news. Preferably Worpress. There is already a very basic page with a simple theme, the logo and little more, I would like something more professional. Www.lamparadebolsillo.com The logo does not want to change.

Target Market(s)

Anyone

Colors

Designer to choose colors to be used in the design.

Requirements
Must have
• You can put the vocalink pluggin with the podcast chapters

```html
<!DOCTYPE html>
<html lang="en">
<head>
<meta charset="utf-8">
<title>Before the kettle boils – Podcast de tecnología</title>
<link href="https://fonts.googleapis.com/css2?family=Roboto:wght@400;500;700&family=Poppins:wght@400;500;600&family=Open+Sans:ital,wght@0,400;0,600;1,400&display=swap" rel="stylesheet">
<style>
:root{
  --orange:#f7931e;
  --orange-deep:#f26522;
  --orange-light:#fbb03b;
  --dark:#1f1f1f;
  --text:#444;
  --muted:#777;
  --line:#e4e4e4;
  --white:#fff;
  --side:#3a2a20;
}
*{box-sizing:border-box;margin:0;padding:0}
html,body{width:1200px;height:2459px;overflow:hidden}
body{background:var(--side);font-family:'Open Sans',sans-serif;color:var(--text);position:relative}
.page{position:absolute;left:92px;top:0;width:1016px;height:2459px;background:var(--white)}
.abs{position:absolute}

/* header */
.site-header{left:0;top:0;width:1016px;height:152px;background:linear-gradient(#2a2a2a,#1b1b1b)}
.social-top{left:23px;top:68px;display:flex;gap:6px}
.social-top span{width:21px;height:21px;border-radius:50%}
.brand{left:0;width:1016px;top:30px;text-align:center;font-family:'Roboto',sans-serif}
.brand .mark{display:block;width:58px;height:58px;border-radius:50%;background:var(--orange);margin:0 auto 8px}
.brand .name{font-size:15px;font-weight:700;color:var(--orange);text-transform:uppercase;letter-spacing:.5px}
.search-top{left:800px;top:57px;width:190px;height:30px;border:2px solid #ddd;border-radius:16px;color:#eee;font-size:12px;padding:5px 14px}
.search-top svg{position:absolute;right:10px;top:7px}
.main-nav{left:0;top:152px;width:1016px;height:46px;background:linear-gradient(var(--orange-light),var(--orange-deep));display:flex;justify-content:center}
.main-nav a{color:#fff;text-decoration:none;font-family:'Roboto',sans-serif;font-weight:500;font-size:16px;text-transform:uppercase;padding:0 24px;line-height:46px;border-right:1px solid rgba(255,255,255,.25)}
.main-nav a:last-child{border:none}

/* hero */
.hero{left:0;top:198px;width:1016px;height:431px;background:radial-gradient(circle at 35% 55%,#5a5a5a,#2d2d2d 55%,#1b1b1b)}
.hero-text{left:668px;top:128px;width:330px;color:#fff}
.hero-text h1{font-family:'Roboto',sans-serif;font-size:38px;line-height:41px;font-weight:700;text-transform:uppercase}
.hero-text p{font-size:14px;line-height:22px;margin-top:10px}
.btn-ghost{display:inline-block;margin-top:18px;border:1px solid #fff;color:#fff;font-size:11px;padding:6px 14px;text-transform:uppercase}
.dots{display:flex;gap:8px;margin-top:20px}
.dots span{width:10px;height:10px;border-radius:50%;background:#fff}
.dots span:first-child{box-shadow:0 0 0 3px rgba(255,255,255,.5)}

/* posts */
.post{left:23px;width:662px;height:339px}
.player{height:69px;display:flex;align-items:center;background:linear-gradient(var(--orange-light),var(--orange-deep));border-top:3px solid #333}
.player .thumb{width:76px;height:66px;background:linear-gradient(135deg,#8a7a6e,#3d3431)}
.player .info{flex:1;padding-left:16px;color:#fff;font-family:'Roboto',sans-serif}
.player .info b{display:block;font-size:21px;font-weight:500}
.player .info small{font-size:14px}
.player .ctrl{display:flex;gap:14px;align-items:center;padding-right:16px}
.post h2{font-family:'Poppins',sans-serif;font-weight:500;font-size:21px;color:#444;margin-top:28px}
.meta{display:flex;gap:30px;font-size:11px;font-style:italic;color:var(--muted);margin-top:12px}
.excerpt{font-size:11.5px;line-height:20px;color:#666;margin-top:14px}
.share{display:flex;gap:6px;margin-top:12px}
.share span{width:22px;height:22px;border-radius:50%}
.more{display:block;margin-top:16px;font-size:10px;color:var(--orange-deep);text-transform:uppercase}

/* sidebar */
.sidebar{left:737px;top:685px;width:253px}
.side-search{height:43px;border:1px solid #ccc;font-size:11px;padding:13px 14px;color:#666;position:relative}
.side-search svg{position:absolute;right:14px;top:15px}
.top10{margin-top:26px;height:169px;background:linear-gradient(135deg,#4a4a4a,#1e1e1e);position:relative}
.top10 b{position:absolute;left:18px;bottom:24px;color:#fff;font-family:'Roboto',sans-serif;font-size:27px;line-height:31px;font-weight:700}
.widget-title{margin-top:32px;height:40px;border-bottom:2px solid var(--orange)}
.widget-title span{display:inline-block;height:40px;line-height:40px;padding:0 42px 0 14px;background:var(--orange-deep);color:#fff;font-family:'Roboto',sans-serif;font-weight:700;font-size:19px;clip-path:polygon(0 0,82% 0,100% 100%,0 100%)}
.recent{display:flex;gap:15px;padding:30px 0 22px;border-bottom:1px solid var(--line)}
.recent .img{width:95px;height:102px;flex:none;background:linear-gradient(135deg,#7b6e66,#2f2a27)}
.recent h4{font-size:13px;font-weight:400;color:#444}
.stars{color:var(--orange);font-size:11px;margin:6px 0}
.recent p{font-size:11px;line-height:17px;color:#666}
.recent small{display:block;margin-top:10px;font-size:11px;font-style:italic;color:#666}
.contact-list{list-style:none;margin-top:22px}
.contact-list li{font-size:13px;color:#555;margin-bottom:14px;display:flex;align-items:center;gap:10px}
.contact-list li::before{content:"";width:11px;height:11px;border-radius:50%;background:#333}
.counts{display:grid;grid-template-columns:repeat(3,77px);gap:10px 11px;margin-top:26px}
.counts div{height:77px;color:#fff;text-align:center;font-size:12px;line-height:15px;padding-top:32px}
.c1{background:#3b5998}.c2{background:#1da1f2}.c3{background:#dc4e41}
.c4{background:#0e76a8}.c5{background:#cd201f}.c6{background:#4a7fd4}

/* footer */
.footer-bg{left:0;top:2082px;width:1016px;height:377px;background:var(--dark)}
.footer-curve{left:0;top:2082px}
.site-footer h3{font-family:'Roboto',sans-serif;font-weight:500;font-size:17px;color:#fff;text-transform:uppercase;white-space:nowrap}
.f-contact{left:23px;top:2158px;width:270px;color:#fff;font-size:13px;line-height:20px}
.f-row{display:flex;gap:16px;margin-top:24px}
.f-row svg{flex:none}
.f-signup{left:328px;top:2158px;width:275px;color:#fff}
.f-signup p{font-size:11px;line-height:19px;margin-top:18px}
.f-signup .field{margin-top:16px;height:39px;background:#fff;color:#555;font-size:11px;padding:12px 14px}
.f-signup .btn{display:inline-block;margin-top:15px;background:var(--orange-deep);color:#fff;font-size:11px;font-weight:600;padding:12px 12px;text-transform:uppercase}
.f-links{left:688px;top:2158px;color:#fff}
.f-links ul{list-style:none;margin-top:20px}
.f-links li{font-size:12px;line-height:23px}
.f-brand{left:822px;top:2190px;width:190px;text-align:center;font-family:'Roboto',sans-serif}
.f-brand .mark{display:block;width:70px;height:70px;border-radius:50%;background:var(--orange);margin:0 auto 10px}
.f-brand .name{font-size:14px;font-weight:700;color:var(--orange);text-transform:uppercase;white-space:nowrap}
.copyright{left:0;top:2424px;width:1016px;text-align:center;color:#fff;font-size:12px}
</style>
</head>
<body>
<div class="page">

  <header class="abs site-header">
    <div class="abs social-top">
      <span style="background:#3b5998"></span><span style="background:#f7b32b"></span><span style="background:#1da1f2"></span><span style="background:#29b6d8"></span><span style="background:#e53935"></span>
    </div>
    <div class="abs brand"><span class="mark"></span><span class="name">Before the kettle boils</span></div>
    <div class="abs search-top">search
      <svg width="12" height="12" viewBox="0 0 12 12"><circle cx="5" cy="5" r="3.5" fill="none" stroke="#fff" stroke-width="1.6"/><line x1="7.6" y1="7.6" x2="11" y2="11" stroke="#fff" stroke-width="1.8"/></svg>
    </div>
  </header>

  <nav class="abs main-nav">
    <a>Home</a><a>About us</a><a>Podcast</a><a>Recent posts</a><a>Blog</a><a>Contact us</a>
  </nav>

  <section class="abs hero" role="img" aria-label="Studio microphone in front of a lit radio mixing desk">
    <div class="abs hero-text">
      <h1>Before the kettle boils</h1>
      <p>Sed ut perspiciatis unde omnis iste natus error sit voluptatem accusantium doloremque</p>
      <span class="btn-ghost">Read more ›</span>
      <div class="dots"><span></span><span></span><span></span><span></span></div>
    </div>
  </section>

  <article class="abs post" style="top:683px">
    <div class="player"><div class="thumb" role="img" aria-label="Episode cover photo"></div>
      <div class="info"><b>Cambio de logo</b><small>Hola a Tod@s!</small></div>
      <div class="ctrl">
        <svg width="20" height="20" viewBox="0 0 20 20" fill="none" stroke="#fff" stroke-width="1.6"><circle cx="15" cy="4" r="2.5"/><circle cx="5" cy="10" r="2.5"/><circle cx="15" cy="16" r="2.5"/><path d="M7 9l6-4M7 11l6 4"/></svg>
        <svg width="20" height="20" viewBox="0 0 20 20" fill="none" stroke="#fff" stroke-width="1.6"><path d="M10 2v11M5 8l5 5 5-5M3 17h14"/></svg>
        <svg width="30" height="30" viewBox="0 0 30 30" fill="none" stroke="#fff" stroke-width="2"><circle cx="15" cy="15" r="13"/><path d="M12 9l9 6-9 6z" fill="#fff"/></svg>
      </div></div>
    <h2>Sed ut perspiciatis unde omnis iste natus</h2>
    <div class="meta"><span>March 25, 2017</span><span>2 comments</span><span>by Marcos</span></div>
    <p class="excerpt">¿Salta a la vista no?, pues sí, renovamos diseño del logo y algo en la web. Aquí los cambios irán poco a poco pero procuraré dejar todo lo que quiero modificar hecho en una semana como mucho, todo dependerá del tiempo que le pueda dedicar aunque lo difícil ya está hecho. Nada más, nos escuchamos en el siguiente!</p>
    <div class="share"><span style="background:#1da1f2"></span><span style="background:#3b5998"></span><span style="background:#dc4e41"></span><span style="background:#cee3f8"></span><span style="background:#2ca5e0"></span><span style="background:#25d366"></span><span style="background:#ef4056"></span><span style="background:#ddd"></span><span style="background:#ddd"></span></div>
    <a class="more">Continue reading &gt;&gt;</a>
  </article>

  <article class="abs post" style="top:1023px">
    <div class="player"><div class="thumb" role="img" aria-label="Episode cover photo"></div>
      <div class="info"><b>Cambio de logo</b><small>Hola a Tod@s!</small></div>
      <div class="ctrl">
        <svg width="20" height="20" viewBox="0 0 20 20" fill="none" stroke="#fff" stroke-width="1.6"><circle cx="15" cy="4" r="2.5"/><circle cx="5" cy="10" r="2.5"/><circle cx="15" cy="16" r="2.5"/><path d="M7 9l6-4M7 11l6 4"/></svg>
        <svg width="20" height="20" viewBox="0 0 20 20" fill="none" stroke="#fff" stroke-width="1.6"><path d="M10 2v11M5 8l5 5 5-5M3 17h14"/></svg>
        <svg width="30" height="30" viewBox="0 0 30 30" fill="none" stroke="#fff" stroke-width="2"><circle cx="15" cy="15" r="13"/><path d="M12 9l9 6-9 6z" fill="#fff"/></svg>
      </div></div>
    <h2>Sed ut perspiciatis unde omnis iste natus</h2>
    <div class="meta"><span>March 25, 2017</span><span>2 comments</span><span>by Marcos</span></div>
    <p class="excerpt">¿Salta a la vista no?, pues sí, renovamos diseño del logo y algo en la web. Aquí los cambios irán poco a poco pero procuraré dejar todo lo que quiero modificar hecho en una semana como mucho, todo dependerá del tiempo que le pueda dedicar aunque lo difícil ya está hecho. Nada más, nos escuchamos en el siguiente!</p>
    <div class="share"><span style="background:#1da1f2"></span><span style="background:#3b5998"></span><span style="background:#dc4e41"></span><span style="background:#cee3f8"></span><span style="background:#2ca5e0"></span><span style="background:#25d366"></span><span style="background:#ef4056"></span><span style="background:#ddd"></span><span style="background:#ddd"></span></div>
    <a class="more">Continue reading &gt;&gt;</a>
  </article>

  <article class="abs post" style="top:1362px">
    <div class="player"><div class="thumb" role="img" aria-label="Episode cover photo"></div>
      <div class="info"><b>Cambio de logo</b><small>Hola a Tod@s!</small></div>
      <div class="ctrl">
        <svg width="20" height="20" viewBox="0 0 20 20" fill="none" stroke="#fff" stroke-width="1.6"><circle cx="15" cy="4" r="2.5"/><circle cx="5" cy="10" r="2.5"/><circle cx="15" cy="16" r="2.5"/><path d="M7 9l6-4M7 11l6 4"/></svg>
        <svg width="20" height="20" viewBox="0 0 20 20" fill="none" stroke="#fff" stroke-width="1.6"><path d="M10 2v11M5 8l5 5 5-5M3 17h14"/></svg>
        <svg width="30" height="30" viewBox="0 0 30 30" fill="none" stroke="#fff" stroke-width="2"><circle cx="15" cy="15" r="13"/><path d="M12 9l9 6-9 6z" fill="#fff"/></svg>
      </div></div>
    <h2>Sed ut perspiciatis unde omnis iste natus</h2>
    <div class="meta"><span>March 25, 2017</span><span>2 comments</span><span>by Marcos</span></div>
    <p class="excerpt">¿Salta a la vista no?, pues sí, renovamos diseño del logo y algo en la web. Aquí los cambios irán poco a poco pero procuraré dejar todo lo que quiero modificar hecho en una semana como mucho, todo dependerá del tiempo que le pueda dedicar aunque lo difícil ya está hecho. Nada más, nos escuchamos en el siguiente!</p>
    <div class="share"><span style="background:#1da1f2"></span><span style="background:#3b5998"></span><span style="background:#dc4e41"></span><span style="background:#cee3f8"></span><span style="background:#2ca5e0"></span><span style="background:#25d366"></span><span style="background:#ef4056"></span><span style="background:#ddd"></span><span style="background:#ddd"></span></div>
    <a class="more">Continue reading &gt;&gt;</a>
  </article>

  <article class="abs post" style="top:1701px">
    <div class="player"><div class="thumb" role="img" aria-label="Episode cover photo"></div>
      <div class="info"><b>Cambio de logo</b><small>Hola a Tod@s!</small></div>
      <div class="ctrl">
        <svg width="20" height="20" viewBox="0 0 20 20" fill="none" stroke="#fff" stroke-width="1.6"><circle cx="15" cy="4" r="2.5"/><circle cx="5" cy="10" r="2.5"/><circle cx="15" cy="16" r="2.5"/><path d="M7 9l6-4M7 11l6 4"/></svg>
        <svg width="20" height="20" viewBox="0 0 20 20" fill="none" stroke="#fff" stroke-width="1.6"><path d="M10 2v11M5 8l5 5 5-5M3 17h14"/></svg>
        <svg width="30" height="30" viewBox="0 0 30 30" fill="none" stroke="#fff" stroke-width="2"><circle cx="15" cy="15" r="13"/><path d="M12 9l9 6-9 6z" fill="#fff"/></svg>
      </div></div>
    <h2>Sed ut perspiciatis unde omnis iste natus</h2>
    <div class="meta"><span>March 25, 2017</span><span>2 comments</span><span>by Marcos</span></div>
    <p class="excerpt">¿Salta a la vista no?, pues sí, renovamos diseño del logo y algo en la web. Aquí los cambios irán poco a poco pero procuraré dejar todo lo que quiero modificar hecho en una semana como mucho, todo dependerá del tiempo que le pueda dedicar aunque lo difícil ya está hecho. Nada más, nos escuchamos en el siguiente!</p>
    <div class="share"><span style="background:#1da1f2"></span><span style="background:#3b5998"></span><span style="background:#dc4e41"></span><span style="background:#cee3f8"></span><span style="background:#2ca5e0"></span><span style="background:#25d366"></span><span style="background:#ef4056"></span><span style="background:#ddd"></span><span style="background:#ddd"></span></div>
    <a class="more">Continue reading &gt;&gt;</a>
  </article>

  <aside class="abs sidebar">
    <div class="side-search">SEARCH
      <svg width="11" height="11" viewBox="0 0 12 12"><circle cx="5" cy="5" r="3.5" fill="none" stroke="#444" stroke-width="1.6"/><line x1="7.6" y1="7.6" x2="11" y2="11" stroke="#444" stroke-width="1.8"/></svg>
    </div>
    <div class="top10" role="img" aria-label="Studio microphone banner"><b>TOP 10<br>PODCAST</b></div>

    <div class="widget-title"><span>RECENT POSTS</span></div>
    <div class="recent"><div class="img" role="img" aria-label="Mixing desk photo"></div><div><h4>Nemo enim ipsam</h4><div class="stars">★★★☆☆</div><p>Lorem ipsum dolor sit amet, consectetur adipiscing elit.</p><small>2 comments</small></div></div>
    <div class="recent"><div class="img" role="img" aria-label="Phone and headphones photo"></div><div><h4>Nemo enim ipsam</h4><div class="stars">★★★☆☆</div><p>Lorem ipsum dolor sit amet, consectetur adipiscing elit.</p><small>2 comments</small></div></div>
    <div class="recent" style="border:none"><div class="img" role="img" aria-label="Listener with headphones photo"></div><div><h4>Nemo enim ipsam</h4><div class="stars">★★★☆☆</div><p>Lorem ipsum dolor sit amet, consectetur adipiscing elit.</p><small>2 comments</small></div></div>

    <div class="widget-title" style="margin-top:26px"><span>CONTACTO</span></div>
    <ul class="contact-list"><li>Chirper</li><li>vocalink</li><li>Audiobox</li><li>Mail</li></ul>

    <div class="counts">
      <div class="c1">68,876<br>Fans</div><div class="c2">65<br>Followers</div><div class="c3">8,961<br>Followers</div>
      <div class="c4">68,876<br>Fans</div><div class="c5">65<br>Followers</div><div class="c6">8,961<br>Followers</div>
    </div>
  </aside>

  <footer class="site-footer">
    <div class="abs footer-bg"></div>
    <svg class="abs footer-curve" width="1016" height="40" viewBox="0 0 1016 40"><path d="M0 0 H1016 V36 Q508 -4 0 36 Z" fill="#fff"/><path d="M0 36 Q508 -4 1016 36" fill="none" stroke="#f7931e" stroke-width="3"/></svg>

    <div class="abs f-contact">
      <h3>Contact us</h3>
      <div class="f-row"><svg width="16" height="20" viewBox="0 0 16 20" fill="none" stroke="#fff" stroke-width="1.5"><path d="M8 19s6-7 6-11A6 6 0 0 0 2 8c0 4 6 11 6 11z"/><circle cx="8" cy="8" r="2"/></svg><span>18 Kettle Lane. Millbrook.<br>TX 70001</span></div>
      <div class="f-row"><svg width="16" height="16" viewBox="0 0 16 16" fill="none" stroke="#fff" stroke-width="1.5"><path d="M3 1h3l1 4-2 1a9 9 0 0 0 5 5l1-2 4 1v3a2 2 0 0 1-2 2A13 13 0 0 1 1 3a2 2 0 0 1 2-2z"/></svg><span>Telephone: +1 555 010 0139<br>Fax: +1 555 010 0142</span></div>
      <div class="f-row"><svg width="16" height="14" viewBox="0 0 16 14" fill="none" stroke="#fff" stroke-width="1.5"><rect x="1" y="2" width="14" height="10"/><path d="M1 2l7 6 7-6"/></svg><span>hello@kettlecast.example</span></div>
    </div>

    <div class="abs f-signup">
      <h3>Sign up to receive email</h3>
      <p>Excepteur sint occaecat cupidatat non proident, sunt in culpa qui Nemo enim ipsam voluptatem</p>
      <div class="field">Enter Name</div>
      <span class="btn">Subscribe</span>
    </div>

    <div class="abs f-links">
      <h3>Quick links</h3>
      <ul><li>Home</li><li>About Us</li><li>Podcast</li><li>Blog</li><li>Events</li><li>Contacts</li></ul>
    </div>

    <div class="abs f-brand"><span class="mark"></span><span class="name">Before the kettle boils</span></div>

    <div class="abs copyright">Copyright © Before the kettle boils 2017. All rights reserved.</div>
  </footer>
</div>
</body>
</html>
```